Stationery Design Project

We need a stationery design for our Norwegian trucking company. We have existed for about 15 years and our 12 drivers uses relatively new vehicles to transport goods around in northern Norway. Long distance routes with fresh fish og food transport is our main operations.

We have already made alogo that's printed on our trucks. The logo and a picture of our trucks is attached. I think the logo i crappy, but since its already in use, changing it is not an option in this round. Still using a better colour scheme in the overall stationery and more interesting fonts is possible (altso in the logo).

Company details:
Name: Kjelvraket AS
Organisation nr 873 615 309
Post adress: 8642 Raudvik

I like minimalism and simplicity. I am avalibly for questions in normal GMT working hours either here or on mail: ivar@fjordlast.no

Reason: Hi. Im extending the deadline because I needed some time to find a vector file of our logo. Sorry for the inconvenience

Hi, and thanks for all your interest in the project. Some updates:

-          I have decided to commit to using one of the designs. Some designer will get the payment.

-          I have extended the deadline with 24 hours since I needed some time to find our firms vector logo (a slow Swedish man was holding me up)

-          We will not choose a design before the deadline. No need to rush.

-          We have received a lot of great design and think there is a need to specified the product we want to make:

o   Business Card for all our employers. I just need the design and will duplicate with the correct numbers and name myself. The information on should be: Logo, employer’s name, Phone number, email, website, Postal number and address. Use this as a template: logo, Leif Brattvoll, 47382066, Leif@fjordlast.no,, fjordlast.no, 8642 Raudvik. The order and placement of the information is your creative decision.

o   Stickers to put on the goods we travel. On the sticker the should be the following information: Logo, phone number, Tekst and link: Fraktæ av Kjelvraket. Ke du syns? Fjordlast.no/tilbakemelding (this means: Handled by Kjelvraket. What do you think Fjordlast.no/feedback -à the link will be a feedback form). The placement the information and size is your creative decision with some stings: we have been thinking of using Drukko for printing and see that a size about 6x6 cm, 8x5 or something like that. (with 3000 copies our budget is 200 punds). Any suggestions of other suppliers are welcome. Drukko price calculator http://www.drukkolabelhouse.co.uk/digital-litho-printing/printing-labels-tags/stickers/

o   Letterhead with logo, address, phone number and organizational number.

o   Envelopes with logo,address, phone number and organizational number.

Have a nice day.

 

 

• Using the blue colour in the logo and using a similar graphic approch.

```html
<!DOCTYPE html>
<html lang="no">
<head>
<meta charset="utf-8">
<title>Kjelvraket AS – visittkort</title>
<link rel="stylesheet" href="https://fonts.googleapis.com/css2?family=Roboto+Condensed:wght@400;700&display=swap">
<style>
  :root {
    --navy: #0f2f8c;
    --sky: #2b86d6;
    --paper: #ffffff;
    --backdrop: #dfe5ea;
    --shadow: rgba(20, 40, 70, 0.18);
  }
  * { margin: 0; padding: 0; box-sizing: border-box; }
  html, body { width: 1200px; height: 960px; overflow: hidden; }
  body {
    background: var(--backdrop);
    font-family: "Roboto Condensed", "Arial Narrow", sans-serif;
    display: flex;
    flex-direction: column;
    align-items: center;
    justify-content: center;
    gap: 60px;
  }
  .card {
    position: relative;
    width: 600px;
    height: 340px;
    background: var(--paper);
    box-shadow: 0 10px 28px var(--shadow);
    overflow: hidden;
  }
  .card-bands { position: absolute; inset: 0; }
  .brand {
    position: absolute;
    display: flex;
    align-items: center;
    gap: 14px;
    color: var(--navy);
    font-weight: 700;
    font-size: 58px;
    letter-spacing: 0.5px;
  }
  .brand-dot {
    width: 26px; height: 26px;
    border-radius: 50%;
    background: var(--sky);
  }
  .card-front .brand { left: 60px; top: 50px; }
  .card-back .brand { left: 50%; top: 80px; transform: translateX(-50%); }
  .company-name {
    position: absolute;
    left: 150px; top: 186px;
    font-size: 30px;
    color: var(--navy);
    letter-spacing: 0.3px;
  }
  .contact {
    position: absolute;
    display: flex;
    align-items: center;
    gap: 8px;
    color: var(--paper);
  }
  .contact svg { width: 16px; height: 16px; fill: currentColor; }
  .contact-phone { left: 175px; top: 269px; font-size: 20px; }
  .contact-address { left: 420px; top: 255px; font-size: 17px; }
  .contact-web { left: 50%; top: 256px; transform: translateX(-50%); font-size: 16px; letter-spacing: 0.8px; }
</style>
</head>
<body>

  <section class="card card-front" aria-label="Visittkort forside">
    <svg class="card-bands" viewBox="0 0 600 340" aria-hidden="true">
      <polygon points="388,248 600,248 600,280 368,280" fill="var(--sky)"/>
      <polygon points="0,268 392,268 372,292 0,292" fill="var(--navy)"/>
      <rect x="0" y="292" width="600" height="20" fill="var(--navy)"/>
    </svg>
    <div class="brand"><span class="brand-dot"></span>Kjelvraket</div>
    <p class="company-name">KJELVRAKET AS</p>
    <p class="contact contact-phone">
      <svg viewBox="0 0 16 16"><path d="M3 1h4l1 4-2 1.5a9 9 0 0 0 3.5 3.5L11 8l4 1v4a2 2 0 0 1-2 2A13 13 0 0 1 1 3a2 2 0 0 1 2-2z"/></svg>
      873 615 309
    </p>
    <p class="contact contact-address">
      <svg viewBox="0 0 16 16"><path d="M8 0a5.5 5.5 0 0 0-5.5 5.5C2.5 10 8 16 8 16s5.5-6 5.5-10.5A5.5 5.5 0 0 0 8 0zm0 8a2.5 2.5 0 1 1 0-5 2.5 2.5 0 0 1 0 5z"/></svg>
      8642 Raudvik
    </p>
  </section>

  <section class="card card-back" aria-label="Visittkort bakside">
    <svg class="card-bands" viewBox="0 0 600 340" aria-hidden="true">
      <rect x="0" y="246" width="600" height="36" fill="var(--navy)"/>
    </svg>
    <div class="brand"><span class="brand-dot"></span>Kjelvraket</div>
    <p class="contact contact-web">
      <svg viewBox="0 0 16 16"><path d="M8 0a8 8 0 1 0 0 16A8 8 0 0 0 8 0zm0 1.5c.9 0 1.9 1.9 2.2 4.5H5.8C6.1 3.4 7.1 1.5 8 1.5zM1.6 7.2h2.9c0 .6 0 1.1.1 1.6H1.6a6.5 6.5 0 0 1 0-1.6zm4.2 0h4.4a14 14 0 0 1 0 1.6H5.8a14 14 0 0 1 0-1.6zm5.7 0h2.9a6.5 6.5 0 0 1 0 1.6h-2.9c.1-.5.1-1 0-1.6zM8 14.5c-.9 0-1.9-1.9-2.2-4.5h4.4c-.3 2.6-1.3 4.5-2.2 4.5z"/></svg>
      www.fjordlast.no
    </p>
  </section>

</body>
</html>
```